Homemaking training schools needs a Business Card design

Designer, Hello!

No special requirements, good-looking enough.
--------------------------------------------------------------------------

Name: Marcus Dole
Chairman
Tel: 0574-71948263
Mobile: 13857420916
Email: kelvora@mailnest.example
Web: www.prt2019.example
Add: No.258, LanpingJie, BeiyuanQu, Ningbo, Zhejiang

LOGO
Ningbo PRT Homemaking Training School

Target Market(s)

pregnant women, mothers, infants, the elderly and families, including cleaning, cooking, nursing training.

Industry/Entity Type

Business

Contact Information for Business Card

Name: Marcus Dole
Chairman
Tel: 0574-71948263
Mobile: 13857420916
Email: kelvora@mailnest.example
Web: www.prt2019.example

LOGO

Font styles to use
Serif
Sans Serif
Decorative

Requirements
Nice to have
• Feels: clean, specifications, safety, comfort, warmth and happiness.

```html
<!DOCTYPE html>
<html lang="en">
<head>
<meta charset="utf-8">
<title>PeiRuiTang Business Card</title>
<link href="https://fonts.googleapis.com/css2?family=Montserrat:wght@600;700&display=swap" rel="stylesheet">
<style>
  :root {
    --bg: #3a3a3a;
    --card: #030303;
    --blue: #1a7fc4;
    --pink: #e6168f;
    --white: #ffffff;
  }
  * { margin: 0; padding: 0; box-sizing: border-box; }
  html, body { width: 1200px; height: 900px; overflow: hidden; }
  body {
    background: var(--bg);
    font-family: "Montserrat", Arial, sans-serif;
    position: relative;
  }
  .card {
    position: absolute;
    left: 280px;
    width: 640px;
    height: 366px;
    background: var(--card);
    border-radius: 22px;
    box-shadow: 0 12px 30px rgba(0,0,0,.45);
    color: var(--white);
    overflow: hidden;
  }
  .card--back { top: 56px; }
  .card--front { top: 474px; }

  .brand-name {
    font-weight: 600;
    color: var(--white);
    text-transform: uppercase;
    letter-spacing: 4px;
    white-space: nowrap;
  }

  /* back side */
  .back-brand {
    position: absolute;
    left: 0; right: 0; top: 150px;
    text-align: center;
    font-size: 30px;
  }
  .back-web {
    position: absolute; right: 30px; bottom: 26px;
    font-size: 17px; font-weight: 600;
  }
  .back-web .accent { color: var(--pink); }

  /* front side */
  .front-brand {
    position: absolute; right: 34px; top: 48px;
    font-size: 24px;
  }
  .contacts {
    position: absolute; right: 30px; top: 150px;
    list-style: none; text-align: right;
    font-size: 13px; font-weight: 600; line-height: 19px;
  }
  .contacts li { display: flex; align-items: center; justify-content: flex-end; gap: 7px; }
  .contacts svg { width: 10px; height: 10px; fill: none; stroke: var(--blue); stroke-width: 1.6; }
  .divider {
    position: absolute; left: 32px; right: 30px; top: 240px;
    height: 2px; background: var(--pink);
  }
  .person { position: absolute; left: 32px; top: 196px; }
  .person-name { font-size: 26px; font-weight: 700; color: var(--blue); line-height: 1; }
  .person-role { font-size: 12px; font-weight: 700; margin-top: 4px; }
  .address {
    position: absolute; left: 32px; top: 286px;
    font-size: 14px; font-weight: 600; line-height: 20px;
  }
</style>
</head>
<body>
  <section class="card card--back">
    <p class="back-brand brand-name">PeiRuiTang</p>
    <p class="back-web">www.<span class="accent">prt2019</span>.example</p>
  </section>

  <section class="card card--front">
    <p class="front-brand brand-name">PeiRuiTang</p>

    <ul class="contacts">
      <li>0574-71948263 <svg viewBox="0 0 10 10"><path d="M2 1 L4 3 L3 4 Q4 6 6 7 L7 6 L9 8 L8 9 Q3 9 1 2 Z"/></svg></li>
      <li>13857420916 <svg viewBox="0 0 10 10"><rect x="2.5" y="0.8" width="5" height="8.4" rx="1"/></svg></li>
      <li>kelvora@mailnest.example <svg viewBox="0 0 10 10"><rect x="0.8" y="2" width="8.4" height="6"/><path d="M1 2 L5 5.5 L9 2"/></svg></li>
      <li>www.prt2019.example <svg viewBox="0 0 10 10"><circle cx="5" cy="5" r="4"/><path d="M1 5 H9 M5 1 Q2 5 5 9 Q8 5 5 1"/></svg></li>
    </ul>

    <div class="person">
      <p class="person-name">MARCUS DOLE</p>
      <p class="person-role">CHAIRMAN</p>
    </div>
    <div class="divider"></div>

    <p class="address">258, LanpingJie<br>BeiyuanQu, Ningbo, Zhejiang</p>
  </section>
</body>
</html>
```